Kinesiology undergraduate program needs an infographic

We would like an infographic to creatively and succinctly inform students, faculty, staff, and others about our undergraduate values and competencies (perhaps also integrating our mission and vision). We would like to see a design that incorporates the definition of Kinesiology (the study of human movement) and the colors of our Westbrook State University at Harlan.

```html
<!DOCTYPE html>
<html lang="en">
<head>
<meta charset="utf-8">
<title>WSUH Kinesiology – Mission, Values, Vision</title>
<link rel="stylesheet" href="https://fonts.googleapis.com/css2?family=Amatic+SC:wght@700&family=Montserrat:wght@800&family=Poppins:wght@400&display=swap">
<style>
  :root {
    --red: #e3262b;
    --navy: #23204a;
    --cyan: #1aa7c9;
    --ink: #1d1d1f;
    --rule: #c9c9cc;
    --rule-dark: #9a9aa0;
    --paper: #ffffff;
    --circle: #e7e7ea;
    --cloud: #ececee;
  }
  * { margin: 0; padding: 0; box-sizing: border-box; }
  html, body { width: 1200px; height: 848px; overflow: hidden; background: var(--paper); }
  .sheet {
    position: relative;
    width: 1200px;
    height: 848px;
    overflow: hidden;
    font-family: "Poppins", sans-serif;
    color: var(--ink);
    background:
      linear-gradient(90deg, transparent 147px, var(--red) 147px, var(--red) 148px, transparent 148px, transparent 159px, var(--red) 159px, var(--red) 160px, transparent 160px),
      repeating-linear-gradient(180deg, transparent 0, transparent 50px, var(--rule) 50px, var(--rule) 51px);
    background-position: 0 0, 0 -3px;
  }
  .strong-rule { position: absolute; left: 0; right: 0; height: 2px; background: var(--rule-dark); }

  .section-title {
    position: absolute;
    font-family: "Amatic SC", sans-serif;
    font-weight: 700;
    color: var(--red);
    font-size: 56px;
    line-height: 1;
    text-align: center;
    letter-spacing: 1px;
  }
  .section-text {
    position: absolute;
    font-size: 16.5px;
    line-height: 20.5px;
    text-align: center;
    color: var(--ink);
  }
  .mission-title { left: 400px; width: 400px; top: 52px; }
  .mission-text { left: 410px; width: 380px; top: 108px; }
  .values-title { left: 94px; width: 280px; top: 188px; }
  .values-text { left: 94px; width: 280px; top: 244px; }
  .values-arrow { position: absolute; left: 218px; top: 338px; }
  .vision-title { left: 838px; width: 280px; top: 188px; }
  .vision-text { left: 838px; width: 280px; top: 244px; }

  .competency { position: absolute; }
  .competency h2 {
    font-family: "Montserrat", sans-serif;
    font-weight: 800;
    font-size: 16px;
    line-height: 20.5px;
    color: var(--navy);
    text-transform: uppercase;
  }
  .competency ul { list-style: none; margin-top: 2px; }
  .competency li { font-size: 16px; line-height: 20.5px; }
  .intrapersonal { left: 124px; top: 492px; }
  .science { left: 124px; top: 651px; }
  .thinking { left: 861px; top: 492px; }
  .relationships { left: 861px; top: 651px; }

  .figure-stage { position: absolute; left: 0; top: 0; }
  .mover {
    position: absolute;
    left: 462px; top: 224px;
    width: 250px; height: 580px;
    border-radius: 110px 110px 40px 40px;
    background: linear-gradient(90deg, var(--red) 0%, #b81f2b 30%, var(--navy) 50%, #c98a6f 50%, #b8664f 100%);
    opacity: .9;
  }
  .graphics { position: absolute; left: 0; top: 0; }
</style>
</head>
<body>
<main class="sheet">
  <div class="strong-rule" style="top:101px"></div>
  <div class="strong-rule" style="top:203px"></div>
  <div class="strong-rule" style="top:356px"></div>

  <svg class="figure-stage" width="1200" height="848" aria-hidden="true">
    <g fill="var(--cloud)">
      <ellipse cx="330" cy="290" rx="22" ry="12"/><ellipse cx="345" cy="282" rx="14" ry="12"/>
      <ellipse cx="838" cy="345" rx="24" ry="13"/><ellipse cx="852" cy="336" rx="15" ry="12"/>
      <ellipse cx="720" cy="250" rx="16" ry="9"/>
    </g>
    <circle cx="584" cy="479" r="211" fill="var(--circle)"/>
    <ellipse cx="584" cy="790" rx="120" ry="28" fill="var(--circle)"/>
  </svg>

  <div class="mover" role="img" aria-label="Illustrated person split down the middle: a student in red hoodie and dark trousers on one side, the human muscular system on the other"></div>

  <svg class="graphics" width="1200" height="848" aria-hidden="true">
    <line x1="572" y1="217" x2="572" y2="821" stroke="var(--navy)" stroke-width="4"/>

    <!-- connectors -->
    <g stroke="var(--ink)" stroke-width="1.2" fill="none">
      <polyline points="356,398 97,398 97,498"/>
      <polyline points="310,665 391,665 391,612 415,612"/>
      <polyline points="784,385 806,385 806,496 832,496"/>
      <polyline points="747,572 804,572 804,661 849,661"/>
    </g>
    <g fill="var(--ink)">
      <circle cx="356" cy="398" r="5"/><circle cx="97" cy="498" r="5"/>
      <circle cx="310" cy="665" r="5"/><circle cx="415" cy="612" r="5"/>
      <circle cx="784" cy="385" r="5"/><circle cx="832" cy="496" r="5"/>
      <circle cx="747" cy="572" r="5"/><circle cx="849" cy="661" r="5"/>
    </g>

    <!-- pencil -->
    <g stroke="var(--navy)" stroke-width="3" fill="none" stroke-linejoin="round">
      <path d="M118 425 L128 417 L166 460 L168 472 L156 468 Z"/>
      <line x1="122" y1="432" x2="132" y2="423"/>
    </g>
    <!-- heartbeat -->
    <polyline fill="none" stroke="var(--navy)" stroke-width="2" points="177,445 218,445 224,430 230,462 236,420 242,452 248,445 298,445 304,430 310,462 316,420 322,452 328,445 378,445 384,430 390,462 396,420 402,452 408,445 428,445"/>

    <!-- atom -->
    <g stroke="var(--navy)" stroke-width="3" fill="none">
      <ellipse cx="78" cy="661" rx="34" ry="13"/>
      <ellipse cx="78" cy="661" rx="34" ry="13" transform="rotate(60 78 661)"/>
      <ellipse cx="78" cy="661" rx="34" ry="13" transform="rotate(-60 78 661)"/>
    </g>
    <circle cx="78" cy="661" r="5" fill="var(--navy)"/>

    <!-- donut charts -->
    <g fill="none" stroke-width="11">
      <circle cx="430" cy="659" r="16" stroke="var(--red)"/>
      <path d="M430 643 A16 16 0 0 1 446 659" stroke="var(--navy)"/>
      <circle cx="427" cy="718" r="16" stroke="var(--red)"/>
      <path d="M427 702 A16 16 0 0 1 440 709" stroke="var(--navy)"/>
      <circle cx="427" cy="775" r="16" stroke="var(--navy)"/>
      <path d="M443 775 A16 16 0 0 1 411 775" stroke="var(--red)"/>
    </g>
    <g fill="#2f6fb8"><circle cx="428" cy="658" r="8"/><circle cx="425" cy="717" r="8"/><circle cx="425" cy="774" r="8"/></g>

    <!-- line chart -->
    <g font-family="Montserrat, sans-serif" font-weight="800" font-size="8" fill="var(--navy)">
      <text x="830" y="408">20:00</text><text x="830" y="423">16:00</text>
      <text x="830" y="438">12:00</text><text x="836" y="452">8:00</text>
      <text x="857" y="468">Mon</text><text x="889" y="468">Tue</text><text x="921" y="468">Wed</text>
      <text x="955" y="468">Thu</text><text x="981" y="468">Fri</text><text x="1017" y="468">Sat</text><text x="1048" y="468">Sun</text>
    </g>
    <polyline points="859,396 859,458 1072,458" fill="none" stroke="var(--navy)" stroke-width="1.5"/>
    <path d="M861 436 C875 432 880 420 892 424 C902 428 900 438 912 434 C922 430 925 420 935 424 C948 428 948 410 960 402 C972 396 976 410 990 412 C1000 414 1000 430 1008 428 C1016 426 1022 402 1034 406 C1044 410 1044 430 1070 434" fill="none" stroke="var(--red)" stroke-width="2.2"/>

    <!-- lightbulb -->
    <g stroke="var(--navy)" stroke-width="3" fill="none" stroke-linecap="round">
      <path d="M1116 485 C1102 474 1104 450 1128 448 C1152 450 1154 474 1140 485 L1138 494 L1118 494 Z"/>
      <line x1="1119" y1="500" x2="1137" y2="500"/><line x1="1122" y1="506" x2="1134" y2="506"/>
      <line x1="1128" y1="436" x2="1128" y2="430"/><line x1="1103" y1="446" x2="1098" y2="441"/>
      <line x1="1153" y1="446" x2="1158" y2="441"/><line x1="1094" y1="468" x2="1088" y2="468"/>
      <line x1="1162" y1="468" x2="1168" y2="468"/>
    </g>

    <!-- gear target -->
    <g stroke="var(--navy)" stroke-width="3" fill="none">
      <circle cx="1094" cy="659" r="32"/><circle cx="1094" cy="659" r="22"/>
      <circle cx="1094" cy="659" r="9"/>
    </g>
    <g stroke="var(--navy)" stroke-width="3">
      <line x1="1094" y1="641" x2="1094" y2="647"/><line x1="1094" y1="671" x2="1094" y2="677"/>
      <line x1="1076" y1="659" x2="1082" y2="659"/><line x1="1106" y1="659" x2="1112" y2="659"/>
      <line x1="1081" y1="646" x2="1085" y2="650"/><line x1="1103" y1="668" x2="1107" y2="672"/>
      <line x1="1107" y1="646" x2="1103" y2="650"/><line x1="1085" y1="668" x2="1081" y2="672"/>
    </g>

    <!-- progress track -->
    <line x1="830" y1="819" x2="952" y2="819" stroke="var(--red)" stroke-width="5"/>
    <line x1="952" y1="819" x2="1075" y2="819" stroke="var(--cyan)" stroke-width="5"/>
    <line x1="1075" y1="819" x2="1200" y2="819" stroke="var(--red)" stroke-width="5"/>
    <circle cx="830" cy="819" r="7" fill="var(--cyan)" stroke="#fff" stroke-width="2"/>
    <circle cx="952" cy="819" r="7" fill="var(--cyan)" stroke="#fff" stroke-width="2"/>
    <circle cx="1075" cy="819" r="7" fill="var(--navy)" stroke="var(--cyan)" stroke-width="2"/>
  </svg>

  <h1 class="section-title mission-title">Our Mission</h1>
  <p class="section-text mission-text">To empower undergraduate students<br>to pursue excellence through<br>scientific discovery, clinical practice,<br>and health promotion</p>

  <h2 class="section-title values-title">Our Values</h2>
  <p class="section-text values-text">Student Success, Science,<br>and Service<br>Our Graduates Will Be<br>Competent In...</p>
  <svg class="values-arrow" width="16" height="14" aria-hidden="true"><path d="M0 0 H16 L8 14 Z" fill="var(--navy)"/></svg>

  <h2 class="section-title vision-title">Our Vision</h2>
  <p class="section-text vision-text">WSUH Kinesiology graduates<br>are leaders who excel in<br>careers that enhance the<br>quality of life of individuals<br>and communities</p>

  <section class="competency intrapersonal">
    <h2>Intrapersonal Growth</h2>
    <ul><li>Cultural Humility/Sensitivity</li><li>Integrity</li><li>Self-Directed</li><li>Dependability</li><li>Mission Oriented</li></ul>
  </section>

  <section class="competency science">
    <h2>The Science of<br>Kinesiology</h2>
    <ul><li>Foundational Concepts of<br>Kinesiology</li><li>Clinical Application</li><li>Scientific Communication</li></ul>
  </section>

  <section class="competency thinking">
    <h2>Thinking and Reasoning</h2>
    <ul><li>Critical Thinking</li><li>Quantitative Reasoning</li><li>Scientific Inquiry</li><li>Concept Integration</li></ul>
  </section>

  <section class="competency relationships">
    <h2>Relationships and<br>Communication</h2>
    <ul><li>Cultural Competence</li><li>Professionalism</li><li>Leadership and Teamwork</li><li>Service</li><li>Orientation/Citizenship</li></ul>
  </section>
</main>
</body>
</html>
```